New Website for World Wide Charity (KOLVAN)

We need a dynamic web design for our brand new charity organisation that will be working worldwide. We will be funded by donations so need to attract people to donate.

What We Do
We work to optimise the wellbeing of the planet, the animals and all that live within. Our slogan is Achieving Vibrational Equilibrium.

We have included a Powerpoint document which may help you understand what we need, it is just an idea for structure and style, it is not set in stone so feel free to be as creative as you like!
Updates

Designs look the same

Target Market(s)

Adults 18+ with an interest in animal, environmental. Businesses that may like to support our natural world or already support our natural world.

Number of Pages Required

3 page

Colors

Designer to choose colors to be used in the design.

Requirements
Must have
• We need the website to be easy to use and understand.

Web pages will be Home, What We Do, Who We Are, Success Stories, What You Can Do (Blog section), Seek Help, Donate, Join.
Nice to have
• Natural feel, easy to navigate, Ideally the website will look natural and organic.

Natural colours, blues, greens, sand, gold, brown, grey, silver, Orange and yellow for impact.
Should not have
• Should not have a dark coloured theme.

```html
<!DOCTYPE html>
<html lang="en">
<head>
<meta charset="utf-8">
<title>Kolvan — Help Raise World Vibration</title>
<link href="https://fonts.googleapis.com/css2?family=Montserrat:ital,wght@0,300;0,400;0,500;0,600;0,700;0,800;1,800&display=swap" rel="stylesheet">
<style>
  :root{
    --navy:#1f3f82;
    --green:#1f5a1f;
    --green-tab:#2a6a22;
    --text-grey:#7a7a7a;
    --white:#ffffff;
    --nav-bg:rgba(48,92,170,.78);
  }
  *{margin:0;padding:0;box-sizing:border-box}
  html,body{width:1200px;height:3485px;overflow:hidden}
  body{position:relative;background:var(--white);font-family:"Montserrat",sans-serif;color:var(--text-grey)}
  .abs{position:absolute}

  .hero-shape{position:absolute;left:0;top:0;width:1200px;height:900px}
  .brand-badge{left:146px;top:10px;width:136px;height:136px;border-radius:50%;background:var(--white);
    box-shadow:0 2px 8px rgba(0,0,0,.25);display:flex;align-items:center;justify-content:center;
    font-weight:700;font-size:20px;color:var(--navy);letter-spacing:1px}
  .main-nav{left:342px;top:58px;width:858px;height:43px;background:var(--nav-bg);display:flex;align-items:center}
  .nav-home{height:43px;width:88px;background:var(--green-tab);clip-path:polygon(22px 0,100% 0,100% 100%,0 100%);
    color:var(--white);font-size:11px;font-weight:600;display:flex;align-items:center;justify-content:center;padding-left:16px}
  .nav-link{color:var(--white);font-size:11px;font-weight:600;margin-left:23px;white-space:nowrap}
  .nav-link:first-of-type{margin-left:24px}
  .btn-donate,.btn-join{position:absolute;top:8px;height:27px;width:73px;border-radius:14px;font-size:10px;font-weight:700;
    color:var(--white);display:flex;align-items:center;justify-content:center}
  .btn-donate{left:562px;background:var(--green)}
  .btn-join{left:640px;border:2px solid var(--white)}

  .hero-title{left:146px;top:250px;font-size:52px;line-height:64px;font-weight:800;color:var(--navy);letter-spacing:.5px}
  .hero-slogan{left:146px;top:404px;font-size:31px;font-weight:800;font-style:italic;color:var(--white);
    text-shadow:0 2px 4px rgba(0,0,0,.6)}
  .btn-pill{border-radius:30px;background:var(--green);color:var(--white);font-weight:700;display:flex;align-items:center;justify-content:center;gap:10px}
  .btn-pill .arrow{width:13px;height:13px}
  .hero-cta{left:145px;top:487px;width:250px;height:55px;font-size:15px}
  .slider-dots{left:568px;top:612px;display:flex;gap:6px}
  .slider-dots span{width:8px;height:8px;border-radius:50%;background:var(--white)}
  .slider-dots span.on{background:transparent;border:1.5px solid var(--white)}

  .focus-circle{border-radius:50%;display:flex;flex-direction:column;align-items:center;justify-content:center;
    box-shadow:0 4px 14px rgba(20,40,90,.25)}
  .focus-circle::after{content:"";position:absolute;inset:12px;border-radius:50%;border:1.5px solid rgba(255,255,255,.45)}
  .focus-label{color:var(--white);font-weight:700;font-size:17px;letter-spacing:.5px;margin-bottom:16px}
  .focus-btn{width:150px;height:40px;font-size:10.5px;position:relative;z-index:1}
  .circle-env{left:149px;top:705px;width:298px;height:298px;background:radial-gradient(circle at 50% 30%,#8fcf5a 0%,#3f8a3c 40%,#2b5e7a 75%,#23468e 100%)}
  .circle-human{left:751px;top:705px;width:298px;height:298px;background:radial-gradient(circle at 50% 35%,#4b6fd0 0%,#2d4fb8 55%,#20418e 100%)}
  .circle-animal{left:439px;top:694px;width:320px;height:320px;background:radial-gradient(circle at 50% 35%,#c9d2e2 0%,#8d9cc0 45%,#3d5a9c 80%,#24458c 100%)}

  .photo{width:400px;height:444px}
  .sec-title{font-size:51px;font-weight:700;color:var(--navy);letter-spacing:1px;line-height:1}
  .sec-copy{font-size:12px;line-height:26.4px;color:var(--text-grey)}
  .sec-copy span{display:block;white-space:nowrap}
  .read-btn{width:165px;height:48px;font-size:14px}

  .photo-env{left:145px;top:1130px;background:linear-gradient(160deg,#b7e35a,#5fa52e 55%,#2f6a1f)}
  .photo-bear{left:655px;top:1779px;background:linear-gradient(170deg,#4f5b3c,#6b4a2e 50%,#3d2a1c 80%,#5a3d22)}
  .photo-human{left:145px;top:2427px;background:linear-gradient(165deg,#c98a1c,#8fa334 50%,#3f6a1e)}
  .mist{left:480px;top:2560px;width:720px;height:520px;background:radial-gradient(ellipse at 50% 60%,rgba(190,200,225,.35),rgba(255,255,255,0) 70%)}

  .footer-shape{position:absolute;left:0;top:2990px;width:1200px;height:495px}
  .footer-badge{left:187px;top:3146px;width:194px;height:194px;border-radius:50%;background:var(--white);
    border:6px solid #dcdcf0;display:flex;align-items:center;justify-content:center;font-size:27px;font-weight:600;color:var(--navy);letter-spacing:1px}
  .foot-col h3{color:var(--white);font-size:20px;font-weight:600;margin-bottom:14px;letter-spacing:.3px}
  .foot-col li{list-style:none;color:var(--white);font-size:13px;line-height:34.5px}
  .foot-copy{left:185px;top:3435px;font-size:12.5px;color:var(--white)}
  .foot-charity{left:641px;top:3433px;font-size:15px;font-weight:700;color:var(--white)}
  .social{top:3425px;width:36px;height:36px;border-radius:50%;border:2px solid var(--white);
    color:var(--white);font-size:9px;font-weight:600;display:flex;align-items:center;justify-content:center}
</style>
</head>
<body>

<svg class="hero-shape" viewBox="0 0 1200 900" role="img" aria-label="Photo of a man with raised arms standing on a rock above misty mountains at sunrise">
  <defs>
    <linearGradient id="sky" x1="0" y1="0" x2="0" y2="1">
      <stop offset="0" stop-color="#4f7fd6"/>
      <stop offset=".22" stop-color="#d9a8d8"/>
      <stop offset=".38" stop-color="#f6c886"/>
      <stop offset=".55" stop-color="#8a8fd0"/>
      <stop offset=".8" stop-color="#2f4f9c"/>
      <stop offset="1" stop-color="#1e3470"/>
    </linearGradient>
  </defs>
  <path d="M0 0H1200V663Q600 1010 0 663Z" fill="url(#sky)"/>
</svg>

<div class="abs brand-badge">KOLVAN</div>

<nav class="abs main-nav">
  <div class="nav-home">HOME</div>
  <span class="nav-link">WHAT WE DO</span>
  <span class="nav-link">WHO WE ARE</span>
  <span class="nav-link">SUCCESS STORIES</span>
  <span class="nav-link">WHAT YOU CAN DO</span>
  <span class="btn-donate">DONATE</span>
  <span class="btn-join">JOIN</span>
</nav>

<h1 class="abs hero-title">HELP RAISE WORLD<br>VIBRATION</h1>
<p class="abs hero-slogan">Achieving Vibrational Equilibrium.</p>
<a class="abs btn-pill hero-cta">MAKE A DIFFERENCE
  <svg class="arrow" viewBox="0 0 14 14"><circle cx="7" cy="7" r="7" fill="#fff"/><path d="M5.5 4l3 3-3 3" stroke="#1f5a1f" stroke-width="2" fill="none"/></svg></a>
<div class="abs slider-dots"><span></span><span></span><span class="on"></span><span></span><span></span></div>

<div class="abs focus-circle circle-env" role="img" aria-label="Photo of a young plant sprouting in green forest">
  <span class="focus-label">ENVIRONMENT</span>
  <a class="btn-pill focus-btn">FIND OUT MORE <svg class="arrow" viewBox="0 0 14 14"><circle cx="7" cy="7" r="6" fill="#fff"/><path d="M5.5 4l3 3-3 3" stroke="#1f5a1f" stroke-width="2" fill="none"/></svg></a>
</div>
<div class="abs focus-circle circle-human" role="img" aria-label="Photo of a person running under a blue sky">
  <span class="focus-label">HUMAN</span>
  <a class="btn-pill focus-btn">FIND OUT MORE <svg class="arrow" viewBox="0 0 14 14"><circle cx="7" cy="7" r="6" fill="#fff"/><path d="M5.5 4l3 3-3 3" stroke="#1f5a1f" stroke-width="2" fill="none"/></svg></a>
</div>
<div class="abs focus-circle circle-animal" role="img" aria-label="Photo of a stag in misty landscape">
  <span class="focus-label" style="margin-top:40px">ANIMAL</span>
  <a class="btn-pill focus-btn">FIND OUT MORE <svg class="arrow" viewBox="0 0 14 14"><circle cx="7" cy="7" r="6" fill="#fff"/><path d="M5.5 4l3 3-3 3" stroke="#1f5a1f" stroke-width="2" fill="none"/></svg></a>
</div>

<div class="abs photo photo-env" role="img" aria-label="Photo of hands holding a glass globe with a seedling over moss"></div>
<h2 class="abs sec-title" style="left:597px;top:1160px">ENVIRONMENT</h2>
<p class="abs sec-copy" style="left:599px;top:1246px">
  <span>Lorem ipsum dolor sit amet, consectetur adipiscing elit, sed do eiusmod</span>
  <span>tempor incididunt ut labore et dolore magna aliquuis ipsum suspendisse</span>
  <span>ultricesommodo viverra maecenas accumsan lacus vel facilisis. Lorem</span>
  <span>ipsum dolor sit amet, consectetur adipiscing elit, sed do eiusmod mpor</span>
  <span>incididunt ut labore et dolore magna aliquuis ipsum susultricesommodo</span>
  <span>viverra maecenas accumsan lacus vel facilisrem ipsum dolor sit amet,</span>
  <span>consectetur adipiscing elit, sed do eiusmod tempor incididunt ut labore</span>
  <span>et dolore magna aliquuis ipsum suspendisse ultrices</span>
</p>
<a class="abs btn-pill read-btn" style="left:599px;top:1491px">READ MORE <svg class="arrow" viewBox="0 0 14 14"><circle cx="7" cy="7" r="6" fill="#fff"/><path d="M5.5 4l3 3-3 3" stroke="#1f5a1f" stroke-width="2" fill="none"/></svg></a>

<h2 class="abs sec-title" style="left:141px;top:1809px">ANIMAL</h2>
<p class="abs sec-copy" style="left:144px;top:1895px">
  <span>Lorem ipsum dolor sit amet, consectetur adipiscing elit, sed do eiusmod</span>
  <span>tempor incididunt ut labore et dolore magna aliquuis ipsum suspendisse</span>
  <span>ultricesommodo viverra maecenas accumsan lacus vel facilisis. Lorem</span>
  <span>ipsum dolor sit amet, consectetur adipiscing elit, sed do eiusmod mpor</span>
  <span>incididunt ut labore et dolore magna aliquuis ipsum susultricesommodo</span>
  <span>viverra maecenas accumsan lacus vel facilisrem ipsum dolor sit amet,</span>
  <span>consectetur adipiscing elit, sed do eiusmod tempor incididunt ut labore</span>
  <span>et dolore magna aliquuis ipsum suspendisse ultrices</span>
</p>
<a class="abs btn-pill read-btn" style="left:144px;top:2140px">READ MORE <svg class="arrow" viewBox="0 0 14 14"><circle cx="7" cy="7" r="6" fill="#fff"/><path d="M5.5 4l3 3-3 3" stroke="#1f5a1f" stroke-width="2" fill="none"/></svg></a>
<div class="abs photo photo-bear" role="img" aria-label="Photo of a brown bear standing in a forest meadow"></div>

<div class="abs mist" role="img" aria-label="Faint misty image of a person with arms raised"></div>
<div class="abs photo photo-human" role="img" aria-label="Photo of a man meditating in sunlit grass"></div>
<h2 class="abs sec-title" style="left:597px;top:2458px">HUMAN</h2>
<p class="abs sec-copy" style="left:599px;top:2544px">
  <span>Lorem ipsum dolor sit amet, consectetur adipiscing elit, sed do eiusmod</span>
  <span>tempor incididunt ut labore et dolore magna aliquuis ipsum suspendisse</span>
  <span>ultricesommodo viverra maecenas accumsan lacus vel facilisis. Lorem</span>
  <span>ipsum dolor sit amet, consectetur adipiscing elit, sed do eiusmod mpor</span>
  <span>incididunt ut labore et dolore magna aliquuis ipsum susultricesommodo</span>
  <span>viverra maecenas accumsan lacus vel facilisrem ipsum dolor sit amet,</span>
  <span>consectetur adipiscing elit, sed do eiusmod tempor incididunt ut labore</span>
  <span>et dolore magna aliquuis ipsum suspendisse ultrices</span>
</p>
<a class="abs btn-pill read-btn" style="left:599px;top:2789px">READ MORE <svg class="arrow" viewBox="0 0 14 14"><circle cx="7" cy="7" r="6" fill="#fff"/><path d="M5.5 4l3 3-3 3" stroke="#1f5a1f" stroke-width="2" fill="none"/></svg></a>

<svg class="footer-shape" viewBox="0 0 1200 495" role="img" aria-label="Faint misty mountain landscape in deep blue">
  <defs>
    <linearGradient id="foot" x1="0" y1="0" x2="0" y2="1">
      <stop offset="0" stop-color="#2b4d92"/>
      <stop offset=".6" stop-color="#2f4f96"/>
      <stop offset="1" stop-color="#253f84"/>
    </linearGradient>
  </defs>
  <path d="M0 250Q600 -170 1200 250V495H0Z" fill="url(#foot)"/>
</svg>

<div class="abs footer-badge">KOLVAN</div>

<div class="abs foot-col" style="left:470px;top:3140px">
  <h3>GET INVOLVED</h3>
  <ul><li>Join Us</li><li>Fundraise</li><li>Donate</li><li>Shop</li></ul>
</div>
<div class="abs foot-col" style="left:687px;top:3140px">
  <h3>GET HELP</h3>
  <ul><li>Contact Us</li><li>Media</li></ul>
</div>
<div class="abs foot-col" style="left:877px;top:3140px">
  <h3>LEGAL</h3>
  <ul><li>Terms and Conditions</li><li>Cookies</li><li>Privacy Policy</li></ul>
</div>

<p class="abs foot-copy">© 2021 Kolvan. All rights reserved.Privacy Terms of Use</p>
<p class="abs foot-charity">CHARITY NUMBER : 4817302</p>
<span class="abs social" style="left:935px">Oro</span>
<span class="abs social" style="left:978px">Vel</span>

</body>
</html>
```